Stylish new business card needed!

Hello everyone! I am in need of a new business card design for an alarm company here in Hurricane WV. I have all fonts, color codes and logos provided for you use! We are a young company and like the style of a clean sleek looking business card. Would like it double sided, one side holding the logo and the other with your design!
Target Market(s)
The people that are looking for the newest tech for home automation and security
Industry/Entity Type
Alarm services; Home automation
Contact Information for Business Card
Name of person; position (Sales; Installer); Phone Number (555.418.7260); Employee cell Number; Website (www.GuardedByVelk.example); Employee Email; Double sided
Look and feel
Each slider illustrates characteristics of the customer's brand and the style your logo design should communicate.

```html
<!DOCTYPE html>
<html lang="en">
<head>
<meta charset="utf-8">
<title>Velk – Business Card</title>
<link rel="stylesheet" href="https://fonts.googleapis.com/css2?family=Archivo+Black&family=Lato:wght@400;700&display=swap">
<style>
  :root {
    --backdrop: #3b3b3d;
    --card: #252628;
    --orange: #ff8c42;
    --grey: #9b9b9b;
    --white: #f4f4f4;
  }
  * { margin: 0; padding: 0; box-sizing: border-box; }
  html, body {
    width: 1200px; height: 937px; overflow: hidden;
    background: var(--backdrop);
  }
  .canvas {
    width: 1200px; height: 937px;
    display: flex; flex-direction: column; align-items: center; justify-content: center;
    gap: 30px;
  }
  .card {
    position: relative;
    width: 756px; height: 432px;
    background: var(--card);
    overflow: hidden;
  }
  .brand {
    display: flex; flex-direction: column; align-items: center;
  }
  .brand-name {
    display: flex; align-items: center; gap: 14px;
    font-family: "Archivo Black", "Arial Black", sans-serif;
    color: var(--orange);
    font-size: 96px; line-height: 1; letter-spacing: 2px;
  }
  .brand-dot {
    width: 26px; height: 26px; border-radius: 50%;
    background: var(--orange);
  }
  .brand-tagline {
    margin-top: 10px;
    font-family: "Archivo Black", "Arial Black", sans-serif;
    color: var(--orange);
    font-size: 13px; letter-spacing: 1px;
  }
  /* Front */
  .card-front { display: flex; align-items: center; justify-content: center; }

  /* Back */
  .card-back .brand {
    position: absolute; left: 70px; top: 150px;
  }
  .card-back .brand-name { font-size: 72px; }
  .card-back .brand-tagline { font-size: 10px; }
  .divider {
    position: absolute; left: 392px; top: 110px;
    width: 1px; height: 190px; background: var(--orange);
  }
  .contact {
    position: absolute; left: 430px; top: 112px;
    font-family: "Lato", Arial, sans-serif; color: var(--white);
  }
  .contact-name {
    font-family: "Archivo Black", "Arial Black", sans-serif;
    color: var(--orange); font-size: 30px; line-height: 1.05;
  }
  .contact-role { font-size: 17px; margin: 4px 0 18px; }
  .contact-list { list-style: none; }
  .contact-list li {
    display: flex; align-items: center; gap: 10px;
    font-size: 17px; line-height: 1.65;
  }
  .contact-list svg { width: 15px; height: 15px; flex: none; fill: var(--orange); }
  .bottom-band {
    position: absolute; left: 0; right: 0; bottom: 0;
    height: 12px; background: var(--orange);
  }
</style>
</head>
<body>
<main class="canvas">
  <section class="card card-front">
    <div class="brand">
      <div class="brand-name"><span class="brand-dot"></span>VELK</div>
      <div class="brand-tagline">AUTOMATION AND SECURITY SERVICES</div>
    </div>
  </section>

  <section class="card card-back">
    <div class="brand">
      <div class="brand-name"><span class="brand-dot"></span>VELK</div>
      <div class="brand-tagline">AUTOMATION AND SECURITY SERVICES</div>
    </div>
    <div class="divider"></div>
    <div class="contact">
      <div class="contact-name">DANA WHITLOCK</div>
      <div class="contact-role">Manager</div>
      <ul class="contact-list">
        <li>
          <svg viewBox="0 0 16 16"><path d="M4 0h8a1.5 1.5 0 0 1 1.5 1.5v13A1.5 1.5 0 0 1 12 16H4a1.5 1.5 0 0 1-1.5-1.5v-13A1.5 1.5 0 0 1 4 0zm0 2v10.5h8V2zm4 11.2a.9.9 0 1 0 0 1.8.9.9 0 0 0 0-1.8z"/></svg>
          000-000-0000
        </li>
        <li>
          <svg viewBox="0 0 16 16"><path d="M3.6 1l2.3 2.8-1.3 1.9c.9 2 2.6 3.7 4.6 4.6l1.9-1.3L14 11.3l-1.6 2.9C6.9 14 2 9.1 1.8 3.6z"/></svg>
          555.418.7260
        </li>
        <li>
          <svg viewBox="0 0 16 16"><path d="M1 3h14v10H1zm1.6 1.5L8 8.6l5.4-4.1z"/></svg>
          mail@GuardedByVelk.example
        </li>
        <li>
          <svg viewBox="0 0 16 16"><circle cx="8" cy="8" r="7"/></svg>
          www.GuardedByVelk.example
        </li>
      </ul>
    </div>
    <div class="bottom-band"></div>
  </section>
</main>
</body>
</html>
```